Freelance Translator in Need of a Business Card

I am a freelance Japanese to English translator. I work in the video game localization industry and do literary translation in my spare time. I would like to have both the English word 'Translator' and the Japanese '翻訳者' in the job title. The final design should evoke trust, openness, and reliability.

Target Market(s)

Video game localization companies
Japanese comic book artists

Industry/Entity Type

Business

Contact Information for Business Card

Daniel Forsvik, Translator
dan.forsvik@quellmail.net
torvenwords.com
twitter: @torven_wd

Colors

Designer to choose colors to be used in the design.

```html
<!DOCTYPE html>
<html lang="en">
<head>
<meta charset="utf-8">
<title>Torven Words – Business Card</title>
<link rel="stylesheet" href="https://fonts.googleapis.com/css2?family=Libre+Baskerville:wght@400;700&family=Noto+Serif+JP:wght@400&display=swap">
<style>
  :root {
    --page-bg: #e6e4e1;
    --card-frame: #111111;
    --card-face: #f4f4f4;
    --card-face-shade: #e4e4e4;
    --ink: #1c1c1c;
    --ink-soft: #4a4a4a;
    --accent: #e8922a;
    --rule: #9a9a9a;
    --back-dark: #2c2c2c;
    --back-mid: #464646;
    --band: #6a6a6a;
    --band-light: #8c8c8c;
    --back-text: #f2f2f2;
  }
  * { margin: 0; padding: 0; box-sizing: border-box; }
  html, body { width: 1200px; height: 892px; overflow: hidden; }
  body {
    background: var(--page-bg);
    display: flex;
    align-items: center;
    justify-content: center;
    gap: 40px;
    font-family: "Libre Baskerville", Georgia, serif;
  }
  .card {
    width: 540px;
    height: 310px;
    position: relative;
    box-shadow: 0 10px 28px rgba(0,0,0,.25);
  }

  /* Front */
  .card-front {
    background: var(--card-frame);
    padding: 14px;
  }
  .card-front .face {
    width: 100%;
    height: 100%;
    background: radial-gradient(ellipse at 45% 40%, var(--card-face) 40%, var(--card-face-shade) 100%);
    position: relative;
  }
  .company-name {
    position: absolute;
    left: 34px;
    bottom: 58px;
    font-size: 25px;
    font-weight: 700;
    color: var(--ink);
    letter-spacing: .2px;
  }
  .divider {
    position: absolute;
    left: 246px;
    top: 64px;
    bottom: 52px;
    width: 1px;
    background: var(--rule);
  }
  .person {
    position: absolute;
    left: 270px;
    top: 40px;
  }
  .person-name {
    font-size: 22px;
    color: var(--ink-soft);
    letter-spacing: .3px;
  }
  .person-title {
    margin-top: 4px;
    font-size: 12px;
    color: var(--accent);
  }
  .person-title .ja { font-family: "Noto Serif JP", serif; margin-left: 4px; }
  .contacts {
    position: absolute;
    left: 270px;
    bottom: 56px;
    list-style: none;
  }
  .contacts li {
    display: flex;
    align-items: center;
    gap: 9px;
    font-size: 12px;
    color: var(--ink-soft);
    line-height: 23px;
  }
  .contacts svg { width: 13px; height: 13px; flex: none; }

  /* Back */
  .card-back {
    background: linear-gradient(135deg, var(--back-mid) 0%, var(--back-dark) 60%, #222 100%);
    overflow: hidden;
  }
  .brand-band {
    position: absolute;
    left: 0;
    right: 0;
    top: 112px;
    height: 86px;
    background: linear-gradient(90deg, var(--band) 0%, var(--band-light) 50%, var(--band) 100%);
    border-top: 3px solid #d8d8d8;
    display: flex;
    align-items: center;
    justify-content: center;
  }
  .brand-band .wordmark {
    font-size: 30px;
    font-weight: 700;
    color: var(--back-text);
    letter-spacing: 1px;
  }
</style>
</head>
<body>
  <section class="card card-front" aria-label="Business card front">
    <div class="face">
      <div class="company-name">Torven Words</div>
      <div class="divider"></div>
      <div class="person">
        <div class="person-name">Daniel Forsvik</div>
        <div class="person-title">Translator<span class="ja">翻訳者</span></div>
      </div>
      <ul class="contacts">
        <li>
          <svg viewBox="0 0 14 14"><circle cx="7" cy="7" r="6" fill="var(--accent)"/></svg>
          @torven_wd
        </li>
        <li>
          <svg viewBox="0 0 14 14"><rect x="1" y="3" width="12" height="8.5" fill="var(--accent)"/><path d="M1 3 L7 8 L13 3" fill="none" stroke="#fff" stroke-width="1"/></svg>
          dan.forsvik@quellmail.net
        </li>
        <li>
          <svg viewBox="0 0 14 14"><circle cx="7" cy="7" r="6" fill="var(--accent)"/><ellipse cx="7" cy="7" rx="2.6" ry="6" fill="none" stroke="#fff" stroke-width=".9"/><line x1="1" y1="7" x2="13" y2="7" stroke="#fff" stroke-width=".9"/></svg>
          www.torvenwords.com
        </li>
      </ul>
    </div>
  </section>

  <section class="card card-back" aria-label="Business card back">
    <div class="brand-band">
      <span class="wordmark">TORVEN WORDS</span>
    </div>
  </section>
</body>
</html>
```